Pastor's Lantern: How To Help Church Leaders Remain Strong In Their Callings.

I have created a 250-page book tentatively entitled, Pastor's Lantern, subtitle: A Handbook To Help Church Leaders Remain Strong in Their Callings. The chapters are taken from my podcast of the same name on TuneVault and website: pastorslantern-example.com which will need updating soon. The purpose of the book is to provide practical solutions to pastors/leaders about everyday issues faced in ministry such as loneliness, financial challenges, a pastor's family problems, sexual temptation ...etc. You can get an idea of the topics from TuneVault.
Updates

As mentioned in the brief, I am looking for something that will communicate solutions. My podcast, Pastor's Lantern from which this material originates is all about practical help for local pastors in facing the challenges of daily ministry. The logo I sent was designed for concept purposes only. It does not need to be on the cover necessarily unless it feeds into the overall theme.

Target Market(s)

Pastors and Church Leaders in the Christian Faith

Industry/Entity Type

Religious

Font styles to use
Serif

Colors

Designer to choose colors to be used in the design.

Requirements
Must have
• Crisp copy and lines. People see covers for 3 seconds. If they are not drawn in by complicated themes, I have failed. Many of the designs so far do not address the topic of the book in a way that impacts. This is about a toolbox or book that provides solutions to their everyday challenges. If it doesn't somehow point to tools, it should instead point to getting solutions.
Nice to have
• I have included a copy of my current logo. If you can incorporate it, fine. If you have a better idea, I am open to that and would be interested in contributing more if the logo is superior. The logo is not essential to either front or back cover..
Should not have
• Simplistic religious themes from often used pics. I will peruse other book covers in my genre. If I find the same pic used, it disqualifies the design immediately no matter how much I like it. Target audience is ministers. Simplistic cross designs have gotten less votes so far in polling. I want to grab attention with a compelling picture that communicates solutions.

```html
<!DOCTYPE html>
<html lang="en">
<head>
<meta charset="utf-8">
<title>Pastor's Lantern – Book Cover</title>
<link href="https://fonts.googleapis.com/css2?family=Cinzel:wght@400;500&display=swap" rel="stylesheet">
<style>
  :root {
    --stone-light: #c2c2be;
    --stone-mid: #8f8e8a;
    --stone-dark: #3a3937;
    --stone-deep: #1e1d1c;
    --iron: #141312;
    --iron-sheen: #6e6c69;
    --rust: #6a3a22;
    --ink-white: #ffffff;
    --text-shadow: rgba(0, 0, 0, 0.6);
  }
  * { margin: 0; padding: 0; box-sizing: border-box; }
  html, body {
    width: 737px;
    height: 1200px;
    overflow: hidden;
    background: var(--stone-dark);
  }
  .cover {
    position: relative;
    width: 737px;
    height: 1200px;
    overflow: hidden;
    font-family: "Cinzel", "Times New Roman", serif;
    color: var(--ink-white);
  }
  .cover-photo {
    position: absolute;
    inset: 0;
    width: 737px;
    height: 1200px;
    display: block;
  }
  .cover-text {
    position: absolute;
    left: 0;
    width: 100%;
    text-align: center;
    text-shadow: 0 2px 6px var(--text-shadow);
    white-space: nowrap;
    font-weight: 400;
  }
  .title-kicker {
    top: 186px;
    font-size: 60px;
    letter-spacing: 0.5em;
    padding-left: 0.5em;
    line-height: 1;
  }
  .title-main {
    top: 268px;
    font-size: 124px;
    letter-spacing: 0.01em;
    line-height: 1;
  }
  .subtitle {
    top: 474px;
    font-size: 24px;
    line-height: 40px;
    letter-spacing: 0.05em;
  }
  .author {
    top: 1100px;
    font-size: 38px;
    letter-spacing: 0.2em;
    padding-left: 0.2em;
    line-height: 1;
  }
</style>
</head>
<body>
  <div class="cover">
    <svg class="cover-photo" viewBox="0 0 737 1200" role="img" aria-label="Close-up photograph of a heavy dark iron chain with rust flecks stretching diagonally from top right to bottom left across a grey concrete surface">
      <defs>
        <radialGradient id="concrete" cx="0.35" cy="0.45" r="0.8">
          <stop offset="0" stop-color="var(--stone-light)"/>
          <stop offset="0.55" stop-color="var(--stone-mid)"/>
          <stop offset="1" stop-color="var(--stone-dark)"/>
        </radialGradient>
        <radialGradient id="concreteRight" cx="0.8" cy="0.7" r="0.45">
          <stop offset="0" stop-color="#cfcfca" stop-opacity="0.9"/>
          <stop offset="1" stop-color="#cfcfca" stop-opacity="0"/>
        </radialGradient>
        <linearGradient id="topShade" x1="0" y1="0" x2="0" y2="1">
          <stop offset="0" stop-color="var(--stone-deep)" stop-opacity="0.85"/>
          <stop offset="0.2" stop-color="var(--stone-deep)" stop-opacity="0"/>
          <stop offset="0.85" stop-color="var(--stone-deep)" stop-opacity="0"/>
          <stop offset="1" stop-color="var(--stone-deep)" stop-opacity="0.55"/>
        </linearGradient>
        <filter id="soft" x="-30%" y="-30%" width="160%" height="160%">
          <feGaussianBlur stdDeviation="28"/>
        </filter>
        <filter id="softer" x="-30%" y="-30%" width="160%" height="160%">
          <feGaussianBlur stdDeviation="14"/>
        </filter>
      </defs>
      <rect class="concrete-base" width="737" height="1200" fill="url(#concrete)"/>
      <rect class="concrete-glow" width="737" height="1200" fill="url(#concreteRight)"/>
      <g class="chain-tones" filter="url(#soft)">
        <path d="M560 -60 C 520 200, 420 420, 330 640 S 150 1050, 90 1280" stroke="var(--iron)" stroke-width="250" fill="none" stroke-linecap="round" opacity="0.55"/>
        <path d="M600 -60 C 560 200, 460 420, 360 640 S 170 1050, 110 1280" stroke="var(--iron)" stroke-width="150" fill="none" stroke-linecap="round" opacity="0.85"/>
      </g>
      <g class="chain-glints" filter="url(#softer)">
        <ellipse cx="520" cy="260" rx="40" ry="18" fill="var(--rust)" opacity="0.7"/>
        <ellipse cx="430" cy="470" rx="34" ry="16" fill="var(--iron-sheen)" opacity="0.7"/>
        <ellipse cx="350" cy="700" rx="44" ry="18" fill="var(--rust)" opacity="0.6"/>
        <ellipse cx="260" cy="880" rx="36" ry="16" fill="var(--iron-sheen)" opacity="0.6"/>
        <ellipse cx="170" cy="1040" rx="40" ry="18" fill="var(--rust)" opacity="0.5"/>
      </g>
      <rect class="vignette" width="737" height="1200" fill="url(#topShade)"/>
    </svg>
    <h1>
      <span class="cover-text title-kicker">PASTOR'S</span>
      <span class="cover-text title-main">LANTERN</span>
    </h1>
    <p class="cover-text subtitle">A HANDBOOK TO HELP CHURCH LEADERS<br>REMAIN STRONG IN THEIR CALLINGS</p>
    <p class="cover-text author">DANA R. WHITFIELD</p>
  </div>
</body>
</html>
```